Chai Tea Company needs a Tea Packaging Box Design

Tea Packaging
Dimensions of the Tea Packaging Box: Height 13 cm; Width 8.5 cm; Depth 7 cm
Individual Teabag Packet/ Sachet: Width 6.5 cm; Length 8.25 cm
We are looking for a new tea packaging design, for our tea business. The material of the box is cardboard. We are also looking for a design that will be on each individual tea bag sachet/packet that goes into the box. This design will be very similar to what you design for the tea packaging box.
Product Info:
Our tea company is called “Velmora Brew”. We sell two types of Chai Tea, once called “Velmora Gold” and one called “Velmora Meadow”. The Velmora Gold has caffeine, while the Velmora Meadow is Naturally Caffeine Free. The Velmora Gold has a black tea base, while the Velmora Meadow has a Rooibos tea base. We will need two tea packaging designs, one for each Chai Tea flavour. The designs for both the teas can be similar, but make sure that you can easily distinguish one from the other (example: make them have different colours or pictures). Both the chai teas, come from the same product line.
Tea Packaging Design:
We are looking for high end tea packaging. We produce high quality teas, and we would like to portray this in our tea packaging. Our teas are made with no artificial flavourings, natural flavourings, or preservatives, so we would also like a natural, organic, high quality look to our tea packaging. Our current logo is a llama. It would be great if you could make the current logo more polished and well made. If you feel that the llama is not well suited or you would like to design the llama differently, we are open to your creative ideas.
General Basic Info:
Keep in mind, we will have both English and French writing on the tea packaging. You do not need to worry about the French writing (we will do the translation), just make sure there is room for it. However, if you feel that you are capable and knowledgeable of incorporating both French and English language into the tea packaging that would be of great help and value.
Back of the Box:
- Will have ingredients and brewing instructions. Basic brewing instructions are: “Add hot water to teabag. Steep for 5-7 minutes, depending on strength preferred. Add milk and your choice of sweetener. Enjoy! See inside panel of box for more detailed instructions”. (The basic brewing instructions, can further be polished or written in a more creative or professional manner).
Front of the Box:
- Will have company name, type of tea, little description of the tea
- 18 teabags
- 54 g (1.9 OZ)
- Should state that this is a product of Alberta, Canada.
Side of the Box:
Any creative wording, slogan, or description about the tea, or whatever you feel would be good on the side of the box.
On the inside flap of the side of the box, there will be detailed instructions on how to brew the tea. These will be different from the simplified brewing instructions on the back of the box. I have attached the advanced brewing instructions as a file. These instructions can further be simplified or reduced to make it easier and cleaner for the consumers to read.
Individual Tea Sachets/ Packets
- These will have a matching look and design of the tea box packaging, except on a smaller scale. Each individual sachet will have the company name, type of tea, little description of the tea in the front of the sachet, while the back will contain the ingredients, and basic brewing instructions.
I have attached a few files, with the dimensions, ingredients, detailed brewing directions, and current logo of the business.
If you have any questions, about the design or packaging please let me know. The winning designer will be required to do a few additional tweaks to finalize the product. Thank you for your time and happy designing!

```html
<!DOCTYPE html>
<html lang="en">
<head>
<meta charset="utf-8">
<title>Velmora Gold – Tea Box Panels</title>
<link rel="stylesheet" href="https://fonts.googleapis.com/css2?family=Playball&family=Montserrat:wght@400;500;600&family=Cormorant+Garamond:wght@400&display=swap">
<style>
  :root {
    --stage: #e4e4e4;
    --paper: #f6f6f4;
    --band-blue: #3f5f8c;
    --band-gold: #b89c62;
    --ink: #2a2a2c;
    --ink-soft: #4a4a4e;
    --slate: #8ea2aa;
    --steel: #3c5566;
    --art-dark: #1e1e20;
  }
  * { box-sizing: border-box; margin: 0; padding: 0; }
  html, body { width: 1200px; height: 1000px; overflow: hidden; }
  body {
    background: var(--stage);
    font-family: "Montserrat", sans-serif;
    color: var(--ink);
    position: relative;
  }
  .panel {
    position: absolute;
    top: 100px;
    width: 523px;
    height: 800px;
    background: var(--paper);
    overflow: hidden;
    box-shadow: 0 2px 10px rgba(0,0,0,0.12);
  }
  .panel--front { left: 47px; }
  .panel--back { left: 630px; }

  .band { position: absolute; top: 0; bottom: 0; width: 62px; }
  .band--blue { background: var(--band-blue); }
  .band--gold { background: var(--band-gold); }
  .band--left { left: 0; }
  .band--right { right: 0; }

  .brand-name {
    position: absolute;
    left: 62px; right: 62px;
    text-align: center;
    font-family: "Montserrat", sans-serif;
    font-weight: 600;
    letter-spacing: 0.08em;
    text-transform: uppercase;
    color: var(--steel);
    white-space: nowrap;
  }

  /* front */
  .front .brand-name--top { top: 92px; font-size: 22px; }
  .product-script {
    position: absolute;
    left: 90px; right: 90px;
    top: 160px;
    font-family: "Playball", cursive;
    font-weight: 400;
    font-size: 78px;
    line-height: 0.92;
    color: var(--slate);
    text-align: center;
  }
  .product-script span { display: block; }
  .product-script span + span { padding-left: 30px; }
  .hero-art {
    position: absolute;
    left: 160px; top: 335px;
    width: 210px; height: 215px;
    background: linear-gradient(180deg, #2e2e30, var(--art-dark));
    border-radius: 8px;
  }
  .front .brand-name--main { top: 578px; font-size: 30px; }
  .count {
    position: absolute; left: 0; right: 0; top: 636px;
    text-align: center;
    font-family: "Cormorant Garamond", serif;
    font-size: 44px;
    line-height: 1;
    color: var(--ink);
  }
  .count-label {
    position: absolute; left: 0; right: 0; top: 692px;
    text-align: center;
    font-size: 15px; letter-spacing: 0.14em;
    color: var(--ink-soft);
  }
  .weight {
    position: absolute; left: 0; right: 0; top: 730px;
    text-align: center;
    font-size: 12px; letter-spacing: 0.08em;
    color: var(--ink-soft);
  }

  /* back */
  .back .brand-name--top { top: 170px; font-size: 28px; }
  .back-copy {
    position: absolute;
    left: 100px; right: 40px; top: 232px;
    font-size: 11.5px;
    line-height: 1.45;
    text-transform: uppercase;
    color: var(--ink);
  }
  .back-copy h2 {
    font-size: 14px; font-weight: 600; letter-spacing: 0.06em;
    text-align: center; margin-bottom: 16px;
  }
  .back-copy .intro { font-size: 13px; letter-spacing: 0.03em; margin-bottom: 16px; }
  .back-copy h3 { font-size: 12px; font-weight: 600; margin: 12px 0 8px; }
  .back-copy ul, .back-copy ol { list-style: none; font-size: 9.5px; line-height: 1.5; color: var(--ink-soft); }
</style>
</head>
<body>
  <section class="panel panel--front front" aria-label="Front panel">
    <div class="band band--blue band--left" role="img" aria-label="Blue woven diamond pattern band"></div>
    <div class="band band--blue band--right" role="img" aria-label="Blue woven diamond pattern band"></div>

    <div class="brand-name brand-name--top">Velmora Brew</div>

    <h1 class="product-script"><span>Velmora</span><span>Gold</span></h1>

    <div class="hero-art" role="img" aria-label="Black silhouette illustration of a walking llama"></div>

    <div class="brand-name brand-name--main">Velmora Brew</div>

    <div class="count">18</div>
    <div class="count-label">TEABAGS</div>
    <div class="weight">54 G (1.9 OZ)</div>
  </section>

  <section class="panel panel--back back" aria-label="Back panel">
    <div class="band band--gold band--left" role="img" aria-label="Gold woven diamond pattern band"></div>

    <div class="brand-name brand-name--top">Velmora Brew</div>

    <div class="back-copy">
      <h2>Velmora Gold</h2>
      <p class="intro">Chai is a rich blend of strong and flavourful tea, aromatic spices, milk and sugar. Authentic chai is an art that requires all natural ingredients, care and time to prepare.</p>
      <h3>For 2 cups:</h3>
      <h3>Ingredients:</h3>
      <ul>
        <li>1½ cups (12 oz) water</li>
        <li>2 chai tea bags</li>
        <li>1 cup (8 oz) whole milk</li>
        <li>2-4 teaspoons sugar or honey to taste</li>
        <li>1-2 teaspoons of sliced or grated fresh ginger (optional)</li>
      </ul>
      <h3>Directions:</h3>
      <ol>
        <li>1. Bring water and tea bags to a low boil in a covered pot.</li>
        <li>2. Turn down heat, keep covered and simmer for 5 minutes. Stir and gently press the bags two or three times to help release flavour.</li>
        <li>3. Add milk and ginger, and stir from time to time while simmering until the chai starts to rise.</li>
        <li>4. Turn off heat, add sugar, stir and allow to sit covered for a further 3 to 5 minutes.</li>
        <li>5. Strain directly from pot into cups and serve. Tea bags may be left in until all the tea is finished.</li>
      </ol>
    </div>
  </section>
</body>
</html>
```